A5 Flyer for Financial Services Business

I am after a re-design of our business flyer to fit in with our new branding style and logo colour scheme. Wanting something with a bit of designer flair that I could not create myself. I have included the flyer which I created which lacks style so dazzle me.

I want to use the same content.

Text for main body of flyer is

Are you a small business owner, tradie or TRPQ Service Provider struggling to stay on top of your bookkeeping and compliance obligations? If so we would love to help you get back on track and take control of your business finances so that you can make informed business decisions and focus on what you do best.

We have over 20 years industry experience and, as a small business ourselves, we are able to offer our clients a personal bookkeeping solution tailored to meet the needs of your business.

Accounts Payable | Accounts Receivable
Customer Invoicing
Bank and Credit Card Reconciliations
Payroll | Superannuation | Payroll Tax
Business Activity | Instalment Activity Statements
Regular Financial Reports
Vantly and Brimfolk Set-Up and Training

```html
<!DOCTYPE html>
<html lang="en">
<head>
<meta charset="utf-8">
<title>Even Keel Financial Services – Bookkeeping Flyer</title>
<link href="https://fonts.googleapis.com/css2?family=Lato:wght@300;400;700;900&display=swap" rel="stylesheet">
<style>
:root{
  --teal:#0b5a78;
  --teal-dark:#084a63;
  --ink:#2b2b2b;
  --grey-light:#f0f0f0;
  --grey-mid:#bdbdbd;
  --paper:#ffffff;
  --backdrop:#e9e9e9;
  --badge-green:#9bc13b;
}
*{margin:0;padding:0;box-sizing:border-box}
html,body{width:1200px;height:1200px;overflow:hidden}
body{background:var(--backdrop);font-family:'Lato',sans-serif;color:var(--ink);position:relative}
.flyer{position:absolute;left:210px;top:62px;width:780px;height:1076px;background:var(--paper);overflow:hidden;box-shadow:0 6px 24px rgba(0,0,0,.18)}

.brand{position:absolute;left:30px;top:108px;width:350px;text-align:center}
.brand-mark{display:inline-block;width:24px;height:24px;border-radius:50%;background:var(--teal);vertical-align:middle;margin-right:10px}
.brand-name{display:inline-block;vertical-align:middle;font-weight:300;font-size:31px;color:var(--teal);letter-spacing:.5px}
.brand-sub{font-weight:300;font-size:15px;color:var(--teal);letter-spacing:7px;margin-top:2px}

.hero-photo{position:absolute;left:400px;top:0;width:380px;height:340px}
.headline-band{position:absolute;left:0;top:176px;width:400px;height:217px;background:linear-gradient(90deg,var(--teal-dark),var(--teal))}
.headline-strip{position:absolute;left:400px;top:330px;width:380px;height:63px;background:var(--teal)}
.headline{position:absolute;left:48px;top:208px;color:#fff;font-weight:900;font-size:39px;line-height:42px;text-transform:uppercase;width:345px}

.about{position:absolute;left:58px;top:440px;width:310px}
.about h2{font-size:27px;font-weight:700;color:var(--ink);margin-bottom:14px}
.about h2 span{color:var(--teal)}
.about p{font-size:16.5px;line-height:22px;font-weight:400;margin-bottom:22px}

.services{position:absolute;left:386px;top:425px;width:356px;height:352px;border-radius:28px;background:linear-gradient(180deg,var(--grey-light),var(--grey-mid))}
.services-corner{position:absolute;left:386px;top:677px}
.services-title{position:absolute;left:432px;top:404px;width:262px;height:44px;background:var(--teal);color:#fff;font-weight:900;font-size:29px;text-align:center;line-height:44px;transform:skewX(-10deg)}
.services-title span{display:inline-block;transform:skewX(10deg)}
.service-list{position:absolute;left:396px;top:468px;width:336px;list-style:none;text-align:right}
.service-list li{font-size:16px;line-height:20px;margin-bottom:13px;padding-right:26px;position:relative}
.service-list li svg{position:absolute;right:0;top:2px}

.accreditations{position:absolute;left:405px;top:802px;list-style:none}
.accreditations li{font-weight:700;font-size:20px;color:var(--teal);line-height:27px;padding-left:28px;position:relative}
.accreditations li svg{position:absolute;left:0;top:6px}
.badge{position:absolute;left:686px;top:792px;width:62px;height:62px;border-radius:50%;background:#fff;border:3px solid #cfd8a0;box-shadow:inset 0 0 0 11px var(--badge-green)}

.call{position:absolute;left:64px;top:895px;width:296px;height:126px;background:var(--grey-light)}
.call-label{position:absolute;left:78px;top:900px;font-size:25px;font-weight:700;color:var(--ink);letter-spacing:1px}
.call-phone{position:absolute;left:48px;top:934px;width:304px;height:54px;background:var(--teal);border-radius:14px 28px 28px 0;color:#fff;font-weight:900;font-size:42px;line-height:54px;padding-left:26px}
.call-agent{position:absolute;left:80px;top:996px;font-size:16px;font-weight:700;color:var(--ink)}

.desk-photo{position:absolute;left:398px;top:868px;width:350px;height:150px;border-radius:38px;border:4px solid #fff;box-shadow:0 2px 8px rgba(0,0,0,.25);background:linear-gradient(135deg,#efe6e0,#c9a68a 55%,#8e6a50)}

.footer{position:absolute;left:0;top:1040px;width:780px;height:36px;background:var(--teal);color:#fff;text-align:center;font-size:18px;line-height:36px;letter-spacing:2px}
</style>
</head>
<body>
<main class="flyer">
  <div class="brand">
    <span class="brand-mark"></span><span class="brand-name">EVEN KEEL</span>
    <div class="brand-sub">Financial Services</div>
  </div>

  <svg class="hero-photo" viewBox="0 0 380 340" role="img" aria-label="Photo of two women meeting at an office desk reviewing documents">
    <defs>
      <linearGradient id="heroTone" x1="0" y1="0" x2="1" y2="1">
        <stop offset="0" stop-color="#c7d3da"/>
        <stop offset=".5" stop-color="#8fa3ae"/>
        <stop offset="1" stop-color="#3f4a55"/>
      </linearGradient>
    </defs>
    <path d="M0 0H380V290C340 330 290 340 210 340H0Z" fill="url(#heroTone)"/>
  </svg>

  <div class="headline-band"></div>
  <div class="headline-strip"></div>
  <h1 class="headline">Bookkeeping tailored to your business needs</h1>

  <section class="about">
    <h2>About <span>Even Keel</span></h2>
    <p>Are you a small business owner, tradie or TRPQ Service Provider struggling to stay on top of your bookkeeping and compliance obligations? If so we would love to help you get back on track and take control of your business finances so that you can make informed business decisions and focus on what you do best.</p>
    <p>We have over 20 years industry experience and, as a small business ourselves, we are able to offer our clients a personal bookkeeping solution tailored to meet the needs of your business.</p>
  </section>

  <div class="services"></div>
  <svg class="services-corner" width="90" height="100" viewBox="0 0 90 100">
    <path d="M0 0V100H90C40 86 10 55 0 0Z" fill="var(--teal)"/>
  </svg>
  <div class="services-title"><span>OUR SERVICES</span></div>
  <ul class="service-list">
    <li>Accounts Payable | Accounts Receivable<svg width="16" height="16" viewBox="0 0 16 16"><rect x="1" y="1" width="14" height="14" fill="none" stroke="#0b5a78" stroke-width="1.6"/><path d="M4 8l3 3 6-7" fill="none" stroke="#0b5a78" stroke-width="1.8"/></svg></li>
    <li>Customer Invoicing<svg width="16" height="16" viewBox="0 0 16 16"><rect x="1" y="1" width="14" height="14" fill="none" stroke="#0b5a78" stroke-width="1.6"/><path d="M4 8l3 3 6-7" fill="none" stroke="#0b5a78" stroke-width="1.8"/></svg></li>
    <li>Bank and Credit Card Reconciliations<svg width="16" height="16" viewBox="0 0 16 16"><rect x="1" y="1" width="14" height="14" fill="none" stroke="#0b5a78" stroke-width="1.6"/><path d="M4 8l3 3 6-7" fill="none" stroke="#0b5a78" stroke-width="1.8"/></svg></li>
    <li>Payroll | Superannuation | Payroll Tax<svg width="16" height="16" viewBox="0 0 16 16"><rect x="1" y="1" width="14" height="14" fill="none" stroke="#0b5a78" stroke-width="1.6"/><path d="M4 8l3 3 6-7" fill="none" stroke="#0b5a78" stroke-width="1.8"/></svg></li>
    <li>Business Activity | Instalment Activity<br>Statements<svg width="16" height="16" viewBox="0 0 16 16"><rect x="1" y="1" width="14" height="14" fill="none" stroke="#0b5a78" stroke-width="1.6"/><path d="M4 8l3 3 6-7" fill="none" stroke="#0b5a78" stroke-width="1.8"/></svg></li>
    <li>Regular Financial Reports<svg width="16" height="16" viewBox="0 0 16 16"><rect x="1" y="1" width="14" height="14" fill="none" stroke="#0b5a78" stroke-width="1.6"/><path d="M4 8l3 3 6-7" fill="none" stroke="#0b5a78" stroke-width="1.8"/></svg></li>
    <li>Vantly &amp; Brimfolk Set-Up &amp; Training<svg width="16" height="16" viewBox="0 0 16 16"><rect x="1" y="1" width="14" height="14" fill="none" stroke="#0b5a78" stroke-width="1.6"/><path d="M4 8l3 3 6-7" fill="none" stroke="#0b5a78" stroke-width="1.8"/></svg></li>
  </ul>

  <ul class="accreditations">
    <li><svg width="17" height="17" viewBox="0 0 16 16"><rect x="1" y="1" width="14" height="14" fill="none" stroke="#0b5a78" stroke-width="1.6"/><path d="M4 8l3 3 6-7" fill="none" stroke="#0b5a78" stroke-width="1.8"/></svg>Vantly Certified Advisor</li>
    <li><svg width="17" height="17" viewBox="0 0 16 16"><rect x="1" y="1" width="14" height="14" fill="none" stroke="#0b5a78" stroke-width="1.6"/><path d="M4 8l3 3 6-7" fill="none" stroke="#0b5a78" stroke-width="1.8"/></svg>Brimfolk Pro Advisor</li>
  </ul>
  <div class="badge" role="img" aria-label="Registered practitioner badge"></div>

  <div class="call"></div>
  <div class="call-label">CALL US NOW</div>
  <div class="call-phone">0400 318 472</div>
  <div class="call-agent">BAS agent: 5107342</div>

  <div class="desk-photo" role="img" aria-label="Photo of hands working with papers and a calculator on a desk"></div>

  <footer class="footer">www.evenkeelfinancialservices.com.au</footer>
</main>
</body>
</html>
```